Bridgeway Health of Nations

Please design a business card that is colorful but at the same time easy to read. We are based out on Miami Florida. We are a small start up healthcare company that has been in operation for 1 year. Our clients are Hospitals, Insurance companies, and Manage Care health companies. We are growing quickly and lead the niche we are in. Please make the card 2 sided on the front will be the typical info. Logo, Company Name, Persons Name, Title, Cell #, Office #, Fax#, email, website. No address. On the back we will list 5 services that we do. For example Care Transitions, Case management, Risk assessment, Utilization Review.
Target Market(s)
CEO's and COO's of hospitals and healthcare companies.
Industry/Entity Type
Healthcare

```html
<!DOCTYPE html>
<html lang="en">
<head>
<meta charset="utf-8">
<title>Bridgeway Health of Nations – Business Card</title>
<link rel="stylesheet" href="https://fonts.googleapis.com/css2?family=Lato:ital,wght@0,400;0,700;0,900;1,700&display=swap">
<style>
  :root {
    --stage: #e9eaec;
    --card: #ffffff;
    --ink: #1d1d1f;
    --ink-soft: #4a4a4e;
    --brand-blue: #2e3192;
    --label-blue: #1f64b4;
    --name-green: #1ca54a;
    --rule: #8a8a8e;
  }
  * { box-sizing: border-box; margin: 0; padding: 0; }
  html, body {
    width: 1200px; height: 926px; overflow: hidden;
    background: var(--stage);
    font-family: "Lato", Arial, sans-serif;
    color: var(--ink);
  }
  .stage {
    width: 1200px; height: 926px;
    display: flex; flex-direction: column;
    align-items: center; justify-content: center; gap: 40px;
  }
  .card {
    position: relative;
    width: 700px; height: 400px;
    background: var(--card);
    overflow: hidden;
    box-shadow: 0 2px 10px rgba(0,0,0,.12);
  }

  /* Front */
  .front__company {
    position: absolute; left: 44px; top: 40px;
    font-size: 32px; font-weight: 400; letter-spacing: .2px;
  }
  .front__person {
    position: absolute; left: 44px; top: 128px;
    font-size: 30px; color: var(--name-green); font-weight: 400;
  }
  .front__person strong { font-weight: 700; }
  .front__title {
    font-size: 17px; font-weight: 900; color: var(--ink);
    letter-spacing: .5px;
  }
  .contact {
    position: absolute; left: 44px; top: 180px;
    list-style: none; font-size: 17px; line-height: 24px;
  }
  .contact__label {
    color: var(--label-blue); font-weight: 700; font-style: italic;
  }
  .front__mark {
    position: absolute; right: -70px; top: 120px;
  }

  /* Back */
  .back__brand {
    position: absolute; left: 120px; top: 56px;
    display: flex; align-items: center; gap: 28px;
  }
  .back__brand-name {
    font-size: 38px; font-weight: 700; line-height: 1.1;
    color: var(--ink-soft); width: 300px;
  }
  .back__rule {
    position: absolute; left: 0; right: 0; height: 1px; background: var(--rule);
  }
  .back__rule--top { top: 228px; }
  .back__rule--bottom { top: 342px; }
  .services {
    position: absolute; left: 0; right: 0; top: 248px;
    text-align: center; text-transform: uppercase;
    font-size: 19px; line-height: 27px; letter-spacing: .6px;
  }
</style>
</head>
<body>
<main class="stage">

  <section class="card front" aria-label="Business card front">
    <h1 class="front__company">Bridgeway Health of Nations</h1>
    <p class="front__person">Marcus <strong>Ellery</strong> <span class="front__title">-TITLE</span></p>
    <ul class="contact">
      <li><span class="contact__label">cell:</span> 305-555-0142</li>
      <li><span class="contact__label">office:</span> 305-555-0187</li>
      <li><span class="contact__label">fax:</span> 305-555-0199</li>
      <li><span class="contact__label">email:</span> marcus@bridgewaynations.com</li>
      <li><span class="contact__label">web:</span> bridgewaynations.com</li>
    </ul>
    <svg class="front__mark" width="400" height="400" viewBox="0 0 400 400" aria-hidden="true">
      <circle cx="200" cy="200" r="190" fill="var(--brand-blue)"/>
    </svg>
  </section>

  <section class="card back" aria-label="Business card back">
    <div class="back__brand">
      <svg width="110" height="110" viewBox="0 0 110 110" aria-hidden="true">
        <circle cx="55" cy="55" r="52" fill="var(--brand-blue)"/>
      </svg>
      <p class="back__brand-name">Bridgeway Health of Nations</p>
    </div>
    <div class="back__rule back__rule--top"></div>
    <p class="services">Care transitions, case management,<br>risk assessment, utilization review and manage care</p>
    <div class="back__rule back__rule--bottom"></div>
  </section>

</main>
</body>
</html>
```